Lumbra Deckworks Company (southern african focus for now) needs a e-commerce website

We need a website design for a playing card company based in Southern Africa/United States. We make locally-sourced playing cards (standard 52 card deck, with customized fronts and backs) for everyone and collaborate with local artists to uplift their talents, while celebrating their nation's culture, heritage, beauty and identity. We would like to see designs that use the colours blue (see flag of Eswatini as starting product), white and some red accents (or your recommendation). The final design should communicate elegance, fun and sustainable prosperity.

Target Market(s)

Everyone loves playing cards. From the solo adventurer to the party host, first time learner or expert, young, middle and old, we need to attract a broad audience that appreciates the finer things and supports sustainable, environmentally contentiousness causes that support the local economy and uplift local talent - thing global, act local.

Number of Pages Required

4 page

Font styles to use
Serif
Sans Serif

Requirements
Must have
• Pages to include Home (Main), About (Our Story), Shop and Contact
Nice to have
• While designs may be static, elements of graceful movement would be desirable. Perhaps functionality of scrolling down on homepage showing playing cards in use, front and back. Quindle and Zorvax store's capture that elegant yet rich look.
Should not have
• Too many products. We focus on 1-2.

```html
<!DOCTYPE html>
<html lang="en">
<head>
<meta charset="utf-8">
<title>Lumbra Playing Cards</title>
<link href="https://fonts.googleapis.com/css2?family=Prata&family=Roboto:wght@400;500;700&display=swap" rel="stylesheet">
<style>
:root{
  --blue:#4061c0;
  --blue-dark:#3553ad;
  --red:#b20d0d;
  --ink:#1f1f1f;
  --muted:#6d6d6d;
  --pale:#f3f3f3;
  --line:#e4e4e4;
  --white:#ffffff;
}
*{margin:0;padding:0;box-sizing:border-box}
html,body{width:1200px;height:4125px;overflow:hidden;background:var(--white)}
body{font-family:'Roboto',sans-serif;color:var(--ink);position:relative}
.page{position:relative;width:1200px;height:4125px;overflow:hidden}
.abs{position:absolute}
.serif{font-family:'Prata',serif;font-weight:400}
.btn{position:absolute;display:flex;align-items:center;justify-content:center;gap:8px;background:var(--blue);color:var(--white);border-radius:24px;font-weight:700;font-size:15px;text-transform:uppercase;letter-spacing:.2px}
.center{left:0;width:1200px;text-align:center}
.art{position:absolute;border-radius:8px}

/* header + hero */
.hero{left:0;top:0;width:1200px;height:662px;background:var(--pale)}
.hero-band{left:0;top:662px;width:1200px;height:11px;background:var(--blue)}
.logo{left:112px;top:40px;font-size:27px;letter-spacing:1px}
.nav{top:48px;font-size:14px;font-weight:500;text-transform:uppercase}
.nav.active{color:var(--blue)}
.nav-underline{left:638px;top:78px;width:52px;height:3px;background:var(--blue)}
.hero-title{left:112px;top:226px;font-size:35px;color:var(--blue);white-space:nowrap}
.hero-title span{color:var(--red)}
.hero-text{left:112px;top:290px;width:420px;font-size:17px;line-height:28px}
.slide-arrow{width:34px;height:34px;border-radius:50%;background:#6e6e6e;display:flex;align-items:center;justify-content:center}

/* sections */
.section-title{font-size:35px}
.lead{left:150px;width:900px;text-align:center;font-size:15px;line-height:27px;color:var(--muted)}
.divider{left:112px;top:1024px;width:977px;height:1px;background:var(--line)}
.product{top:1155px;width:290px;height:367px;background:var(--pale)}
.product-cap{position:absolute;left:0;bottom:38px;width:100%;text-align:center;color:var(--blue);font-weight:500;font-size:16px}
.feature-pale{background:var(--pale)}
.feature-label{font-size:18px}
.feature-title{font-size:33px;letter-spacing:.5px;white-space:nowrap}
.feature-text{width:370px;font-size:15.5px;line-height:27.5px;color:var(--muted)}

/* faq */
.faq{position:absolute;border:1px solid var(--line);background:var(--white)}
.faq-head{height:45px;display:flex;align-items:center;padding:0 20px;font-size:14.5px;font-weight:500;gap:10px}
.faq-head .q{flex:1}
.faq-body{border-top:1px solid var(--line);padding:14px 22px;font-size:13px;line-height:22px;color:var(--muted)}

/* cta + footer */
.cta{left:0;top:3247px;width:1200px;height:498px;background:linear-gradient(#fafafa,#eef1f9)}
.footer{left:0;top:3745px;width:1200px;height:380px;background:var(--blue);color:var(--white)}
.f-head{font-size:16px;font-weight:500;text-transform:uppercase;letter-spacing:.3px}
.f-list{font-size:12px;line-height:22.5px;list-style:none}
.contact-row{display:flex;align-items:center;gap:10px;font-size:12px;margin-bottom:13px}
.dot-red{width:11px;height:11px;border-radius:2px;background:#d8262c;flex:none}
.email-box{left:615px;top:3897px;width:266px;height:36px;border-radius:20px;background:var(--white);color:#777;font-size:13px;display:flex;align-items:center;padding-left:17px}
.email-send{position:absolute;right:3px;top:3px;width:30px;height:30px;border-radius:50%;background:#d8262c;display:flex;align-items:center;justify-content:center}
.pay{top:3953px;width:27px;height:17px;border-radius:3px;background:#e9eefb}
.social{top:4026px;width:34px;height:34px;border:2px solid var(--white);border-radius:50%}
</style>
</head>
<body>
<div class="page">

  <!-- Hero -->
  <div class="abs hero"></div>
  <div class="abs hero-band"></div>
  <div class="abs logo serif">Lumbra</div>
  <div class="abs nav-underline"></div>
  <div class="abs nav active" style="left:642px">Home</div>
  <div class="abs nav" style="left:728px">About</div>
  <div class="abs nav" style="left:820px">Shop</div>
  <div class="abs nav" style="left:903px">Contact</div>
  <div class="abs" style="left:1011px;top:49px;width:24px;height:14px;background:linear-gradient(#c8334a 0 50%,#eef 50%);border-radius:1px"></div>
  <div class="abs" style="left:1042px;top:49px;font-size:11px">(EN)</div>
  <svg class="abs" style="left:1072px;top:53px" width="10" height="6"><path d="M0 0h10L5 6z" fill="#222"/></svg>

  <h1 class="abs hero-title serif">Lumbra <span>Playing Card</span></h1>
  <p class="abs hero-text">Lorem ipsum dolor sit amet, consectetur adipiscing elit, sed do eiusmod tempor</p>
  <div class="btn" style="left:112px;top:373px;width:176px;height:52px">Get Your Card</div>
  <div class="abs slide-arrow" style="left:35px;top:331px"><svg width="12" height="12"><path d="M8 1 3 6l5 5" stroke="#fff" stroke-width="2" fill="none"/></svg></div>
  <div class="abs slide-arrow" style="left:1131px;top:331px"><svg width="12" height="12"><path d="M4 1l5 5-5 5" stroke="#fff" stroke-width="2" fill="none"/></svg></div>
  <div class="art" role="img" aria-label="Fan of four aces beside a deck back in blue and red" style="left:580px;top:120px;width:520px;height:535px;background:linear-gradient(120deg,#fbfbfb 0%,#e6e6e6 45%,#8fa3dc 75%,#4061c0 100%)"></div>

  <!-- Welcome -->
  <h2 class="abs center section-title serif" style="top:756px">Welcome To Lumbra</h2>
  <p class="abs lead" style="top:820px">Sed ut perspiciatis unde omnis iste natus error sit voluptatem accusantium doloremque laudantium, totam rem aperiam, eaque ipsa quae ab illo inventore veritatis et quasi architecto beatae vitae dicta sunt explicabo. Nemo enim ipsam voluptatem quia voluptas sit aspernatur aut odit aut fugit, sed quia consequuntur magni dolores eos qui ratione voluptatem sequi nesciunt.</p>
  <div class="btn" style="left:519px;top:932px;width:163px;height:45px">Read More
    <svg width="14" height="14"><circle cx="7" cy="7" r="7" fill="#fff"/><path d="M5.5 4l3 3-3 3" stroke="#4061c0" stroke-width="1.8" fill="none"/></svg></div>
  <div class="abs divider"></div>

  <!-- Products -->
  <h2 class="abs center section-title serif" style="top:1073px">Our Playing Cards</h2>
  <svg class="abs" style="left:45px;top:1316px" width="30" height="60"><path d="M30 0v60L0 30z" fill="var(--red)"/></svg>
  <svg class="abs" style="left:1110px;top:1316px" width="30" height="60"><path d="M0 0v60l30-30z" fill="var(--red)"/></svg>

  <div class="abs product" style="left:133px">
    <div class="art" role="img" aria-label="Ace fan with a deck back showing a traditional drum maker" style="left:20px;top:30px;width:250px;height:230px;background:linear-gradient(120deg,#f6f6f6 20%,#b59a7a 70%,#6a5238)"></div>
    <div class="product-cap">Lorem ipsum dolor sit amet</div>
  </div>
  <div class="abs product" style="left:452px">
    <div class="art" role="img" aria-label="Ace fan with a deck back showing a colourful turaco bird" style="left:20px;top:30px;width:250px;height:230px;background:linear-gradient(120deg,#f6f6f6 20%,#7fa65e 70%,#3a6fa8)"></div>
    <div class="product-cap">Lorem ipsum dolor sit amet</div>
  </div>
  <div class="abs product" style="left:772px">
    <div class="art" role="img" aria-label="Ace fan with a deck back showing white wild flowers" style="left:20px;top:30px;width:250px;height:230px;background:linear-gradient(120deg,#f6f6f6 20%,#7d9466 70%,#4c6a3a)"></div>
    <div class="product-cap">Lorem ipsum dolor sit amet</div>
  </div>

  <!-- Feature 1 -->
  <div class="abs" style="left:0;top:1652px;width:110px;height:373px;background:var(--blue)"></div>
  <div class="abs feature-pale" style="left:599px;top:1652px;width:601px;height:373px"></div>
  <div class="art" role="img" aria-label="Ace fan with a deck back showing a national flower" style="left:700px;top:1680px;width:400px;height:325px;background:linear-gradient(120deg,#fbfbfb 20%,#9db08a 70%,#5e7a4a)"></div>
  <div class="abs feature-label" style="left:183px;top:1682px">The National Flower</div>
  <h3 class="abs feature-title serif" style="left:183px;top:1710px">King Lumbra Deck</h3>
  <p class="abs feature-text" style="left:183px;top:1779px">Sed ut perspiciatis unde omnis iste natus error sit voluptatem accusantium doloremque laudantium, totam rem aperiam, eaque ipsa quae ab illo inventore veritatis et quasi architecto beatae vitae dicta sunt explicabo.</p>
  <div class="btn" style="left:183px;top:1946px;width:171px;height:45px">See Collection</div>

  <!-- Feature 2 -->
  <div class="abs feature-pale" style="left:0;top:2025px;width:599px;height:373px"></div>
  <div class="art" role="img" aria-label="Ace fan with a deck back showing an elephant" style="left:105px;top:2055px;width:400px;height:325px;background:linear-gradient(120deg,#fbfbfb 20%,#a8957e 70%,#6f7a4e)"></div>
  <div class="abs" style="left:1089px;top:2025px;width:111px;height:373px;background:var(--red)"></div>
  <div class="abs feature-label" style="left:670px;top:2055px">Big Five Series</div>
  <h3 class="abs feature-title serif" style="left:670px;top:2083px">Elephant Deck</h3>
  <p class="abs feature-text" style="left:670px;top:2152px">Sed ut perspiciatis unde omnis iste natus error sit voluptatem accusantium doloremque laudantium, totam rem aperiam, eaque ipsa quae ab illo inventore veritatis et quasi architecto beatae vitae dicta sunt explicabo.</p>
  <div class="btn" style="left:670px;top:2319px;width:172px;height:45px">See Collection</div>

  <!-- Feature 3 -->
  <div class="abs" style="left:0;top:2398px;width:110px;height:372px;background:var(--blue)"></div>
  <div class="abs" role="img" aria-label="Video still of a waterfall over rocks" style="left:599px;top:2398px;width:601px;height:372px;background:linear-gradient(160deg,#5d6a3c 0%,#8a7a62 45%,#b9a68e 70%,#8c8470 100%)"></div>
  <svg class="abs" style="left:862px;top:2555px" width="74" height="74"><circle cx="37" cy="37" r="34" stroke="#e6e6e6" stroke-width="4" fill="none" opacity=".8"/><path d="M29 22v30l24-15z" fill="#e6e6e6" opacity=".8"/></svg>
  <div class="abs feature-label" style="left:183px;top:2429px">About Us</div>
  <h3 class="abs feature-title serif" style="left:183px;top:2457px">Lumbra Playing Card</h3>
  <p class="abs feature-text" style="left:183px;top:2526px">Sed ut perspiciatis unde omnis iste natus error sit voluptatem accusantium doloremque laudantium, totam rem aperiam, eaque ipsa quae ab illo inventore veritatis et quasi architecto beatae vitae dicta sunt explicabo.</p>
  <div class="btn" style="left:183px;top:2692px;width:171px;height:45px">Read More</div>

  <!-- FAQ -->
  <h2 class="abs center serif" style="top:2866px;font-size:32px">FAQ</h2>
  <div class="abs center" style="top:2913px;font-size:15px">Frequently Asked Questions</div>

  <div class="faq" style="left:112px;top:2967px;width:470px">
    <div class="faq-head"><svg width="14" height="12"><ellipse cx="7" cy="5" rx="7" ry="5" fill="#111"/><path d="M2 8 1 12l5-3z" fill="#111"/></svg><span class="q">Lorem ipsum dolor sit amet, consectetur elit</span><svg width="12" height="12"><circle cx="6" cy="6" r="6" fill="#d8262c"/><rect x="3" y="5" width="6" height="2" fill="#fff"/></svg></div>
    <div class="faq-body">Sed ut perspiciatis unde omnis iste natus error sit voluptatem accusantium doloremque laudantium, totam rem aperiam, eaque ipsa quae ab illo inventore</div>
  </div>
  <div class="faq" style="left:112px;top:3124px;width:470px">
    <div class="faq-head"><svg width="14" height="12"><ellipse cx="7" cy="5" rx="7" ry="5" fill="#111"/><path d="M2 8 1 12l5-3z" fill="#111"/></svg><span class="q">Lorem ipsum dolor sit amet, consectetur elit</span><svg width="12" height="12"><circle cx="6" cy="6" r="6" fill="#111"/><path d="M3 6h6M6 3v6" stroke="#fff" stroke-width="2"/></svg></div>
  </div>
  <div class="faq" style="left:617px;top:2967px;width:471px">
    <div class="faq-head"><svg width="14" height="12"><ellipse cx="7" cy="5" rx="7" ry="5" fill="#111"/><path d="M2 8 1 12l5-3z" fill="#111"/></svg><span class="q">Lorem ipsum dolor sit amet, consectetur elit</span><svg width="12" height="12"><circle cx="6" cy="6" r="6" fill="#111"/><path d="M3 6h6M6 3v6" stroke="#fff" stroke-width="2"/></svg></div>
  </div>
  <div class="faq" style="left:617px;top:3042px;width:471px">
    <div class="faq-head"><svg width="14" height="12"><ellipse cx="7" cy="5" rx="7" ry="5" fill="#111"/><path d="M2 8 1 12l5-3z" fill="#111"/></svg><span class="q">Lorem ipsum dolor sit amet, consectetur elit</span><svg width="12" height="12"><circle cx="6" cy="6" r="6" fill="#111"/><path d="M3 6h6M6 3v6" stroke="#fff" stroke-width="2"/></svg></div>
  </div>
  <div class="faq" style="left:617px;top:3118px;width:471px">
    <div class="faq-head"><svg width="14" height="12"><ellipse cx="7" cy="5" rx="7" ry="5" fill="#111"/><path d="M2 8 1 12l5-3z" fill="#111"/></svg><span class="q">Lorem ipsum dolor sit amet, consectetur elit</span><svg width="12" height="12"><circle cx="6" cy="6" r="6" fill="#111"/><rect x="3" y="5" width="6" height="2" fill="#fff"/></svg></div>
  </div>

  <!-- CTA -->
  <div class="abs cta" role="img" aria-label="Soft pattern of small blue birds"></div>
  <h2 class="abs center serif" style="top:3283px;font-size:34px;letter-spacing:.5px">Lumbra Play Cards</h2>
  <div class="btn" style="left:508px;top:3350px;width:182px;height:45px">Get Your Card</div>
  <div class="abs" role="img" aria-label="Brand crest emblem" style="left:452px;top:3436px;width:288px;height:330px;border-radius:10px;background:linear-gradient(180deg,#d9dfef 0%,#9fb0de 100%)"></div>

  <!-- Footer -->
  <div class="abs footer"></div>
  <div class="abs f-head" style="left:112px;top:3843px;color:#fff">Contact Info</div>
  <div class="abs" style="left:112px;top:3877px;color:#fff">
    <div class="contact-row"><span class="dot-red"></span>(555) 010-4100</div>
    <div class="contact-row"><span class="dot-red"></span>(555) 010-4100</div>
    <div class="contact-row"><span class="dot-red"></span><u>hello@lumbradeck.com</u></div>
    <div class="contact-row" style="align-items:flex-start"><svg width="11" height="13" style="flex:none"><path d="M5.5 0a5 5 0 0 1 5 5c0 4-5 8-5 8S.5 9 .5 5a5 5 0 0 1 5-5z" fill="#d8262c"/></svg><span>#2868 Lorem ipsum dolor sit<br>amet, consectetur</span></div>
  </div>

  <div class="abs f-head" style="left:405px;top:3843px;color:#fff">Quick Links</div>
  <ul class="abs f-list" style="left:405px;top:3875px;color:#fff"><li>Home</li><li>About</li><li>Shop</li><li>Contact</li></ul>

  <div class="abs f-head" style="left:615px;top:3843px;color:#fff">Newsletter Subscription</div>
  <div class="abs email-box">Enter your email
    <div class="email-send"><svg width="14" height="14"><path d="M1 7 13 1 9 13 7 8z" fill="#fff"/></svg></div>
  </div>
  <div class="abs pay" style="left:615px"></div>
  <div class="abs pay" style="left:647px"></div>
  <div class="abs pay" style="left:679px"></div>
  <div class="abs pay" style="left:711px"></div>
  <div class="abs pay" style="left:743px"></div>

  <div class="abs f-head" style="left:966px;top:3843px;color:#fff">Important</div>
  <ul class="abs f-list" style="left:966px;top:3885px;color:#fff">
    <li>» Terms of Use</li><li>» Site Map</li><li>» Privacy Policy</li><li>» Disclaimer</li>
  </ul>

  <div class="abs social" style="left:522px"></div>
  <div class="abs social" style="left:563px"></div>
  <div class="abs social" style="left:603px"></div>
  <div class="abs social" style="left:643px"></div>
  <div class="abs center" style="top:4082px;font-size:12.5px;color:#fff">© Copyright 2020 lumbra, All Rights Reserved</div>

</div>
</body>
</html>
```